Dentistry

Dentist's personal business card. No logo needed. The card shoul deliver the massage of reliability, professionalism, experience.
Please ad the full brief of the project: down the line it says: the winning look should be precise and pristine NO pictures of Teeth, smiles, instruments etc.

The details to be desplaid are:
Dr. Rob Tavolen
Doctor of Dental Surgery
PHD
Web. Www.drtavolen.com
Email. Rob@drtavolen.com
Tel 07742318590
Surgery address. 27Bferndale road London SW4 8QT UK
62 Wexley Row London SW3 2HN. Uk

Reason: Decided to make the payment unrefundable in order to get more designers involved.

Requirements
Should not have
• Logo, teeth, smile any sort of instruments.

```html
<!DOCTYPE html>
<html lang="en">
<head>
<meta charset="utf-8">
<title>Dr. Rob Tavolen – Business Card</title>
<link rel="stylesheet" href="https://fonts.googleapis.com/css2?family=Arimo:wght@400;700&family=Open+Sans:wght@400&display=swap">
<style>
  :root {
    --canvas: #eceeee;
    --card: #ffffff;
    --navy: #1650a0;
    --band: #0d4ea3;
    --sky: #27b4e8;
    --rule: #5577b8;
    --shadow: rgba(0, 0, 0, 0.28);
  }
  * { box-sizing: border-box; margin: 0; padding: 0; }
  html, body {
    width: 1025px; height: 1200px; overflow: hidden;
    background: var(--canvas);
  }
  .canvas { position: relative; width: 1025px; height: 1200px; }
  .card {
    position: absolute; left: 74px; width: 857px; height: 475px;
    background: var(--card); border-radius: 29px; overflow: hidden;
    box-shadow: 2px 4px 10px var(--shadow);
  }
  .card--front { top: 90px; font-family: "Arimo", Arial, sans-serif; color: var(--navy); }
  .card--back { top: 632px; font-family: "Open Sans", Arial, sans-serif; }

  .identity { position: absolute; top: 50px; left: 0; width: 100%; text-align: center; }
  .identity__name { font-size: 26px; font-weight: 700; line-height: 34px; }
  .identity__title { font-size: 27px; line-height: 34px; }

  .contact { position: absolute; display: flex; align-items: center; gap: 10px; font-size: 25px; font-weight: 700; }
  .contact--phone { left: 356px; top: 169px; }
  .contact--email { left: 356px; top: 215px; }
  .contact svg { flex: none; }

  .addresses { position: absolute; left: 252px; top: 272px; display: flex; gap: 14px; align-items: center; }
  .addresses__lines { font-size: 22px; line-height: 29px; }

  .wave { position: absolute; left: 0; top: 0; }
  .website {
    position: absolute; left: 0; width: 100%; top: 402px; text-align: center;
    color: #fff; font-size: 29px; font-weight: 700;
  }

  .appointment__label { position: absolute; left: 107px; top: 100px; font-size: 24px; color: var(--navy); }
  .appointment__line { position: absolute; left: 107px; width: 642px; height: 1.5px; background: var(--rule); }
</style>
</head>
<body>
<main class="canvas">
  <section class="card card--front" aria-label="Business card front">
    <svg class="wave" width="857" height="475" viewBox="0 0 857 475" aria-hidden="true">
      <path d="M0,346 C200,300 420,382 610,388 C730,390 810,372 857,364 L857,475 L0,475 Z" fill="var(--band)"/>
      <path d="M520,372 C660,380 780,348 857,326 L857,360 C780,378 660,392 520,378 Z" fill="var(--sky)"/>
      <path d="M0,372 C120,352 240,340 360,344" fill="none" stroke="#ffffff" stroke-width="5"/>
    </svg>

    <div class="identity">
      <p class="identity__name">Dr. Rob Tavolen</p>
      <p class="identity__title">Doctor of Dental Surgery</p>
      <p class="identity__title">PHD</p>
    </div>

    <p class="contact contact--phone">
      <svg width="20" height="20" viewBox="0 0 24 24" aria-hidden="true"><path d="M6.6 10.8c1.4 2.8 3.8 5.1 6.6 6.6l2.2-2.2c.3-.3.7-.4 1-.2 1.1.4 2.3.6 3.6.6.6 0 1 .4 1 1V20c0 .6-.4 1-1 1C10.6 21 3 13.4 3 4c0-.6.4-1 1-1h3.5c.6 0 1 .4 1 1 0 1.3.2 2.5.6 3.6.1.3 0 .7-.2 1z" fill="var(--navy)"/></svg>
      <span>07742318590</span>
    </p>
    <p class="contact contact--email">
      <svg width="22" height="16" viewBox="0 0 22 16" aria-hidden="true"><rect x="1" y="1" width="20" height="14" fill="none" stroke="var(--navy)" stroke-width="1.6"/><path d="M1 1l10 8 10-8" fill="none" stroke="var(--navy)" stroke-width="1.6"/></svg>
      <span>rob@drtavolen.com</span>
    </p>

    <div class="addresses">
      <svg width="24" height="16" viewBox="0 0 24 16" aria-hidden="true"><path d="M2 10c3-5 7-7 10-7s7 2 10 7" fill="none" stroke="var(--navy)" stroke-width="2.4"/><circle cx="12" cy="10" r="3.5" fill="var(--navy)"/></svg>
      <p class="addresses__lines">27Bferndale road London SW4 8QT UK<br>62 Wexley Row London SW3 2HN. Uk</p>
    </div>

    <p class="website">www.drtavolen.com</p>
  </section>

  <section class="card card--back" aria-label="Business card back">
    <p class="appointment__label">Your next appointment</p>
    <div class="appointment__line" style="top:183px"></div>
    <div class="appointment__line" style="top:226px"></div>
    <div class="appointment__line" style="top:269px"></div>
    <div class="appointment__line" style="top:313px"></div>
  </section>
</main>
</body>
</html>
```